Card design for orthopaedic surgeons working as The Brightwater Joint Centre

Business cards, letterhead

Colors

Designer to choose colors to be used in the design.

Requirements
Must have
• Late addition.
• Cards letterhead must have logos of
• Crestmoor Lindell College of Surgeons
• Varenwood Bone Health Association
Nice to have
• Back of card to have space for appointment time to be added by hand and some blank space for writing incidental other notes.

```html
<!DOCTYPE html>
<html lang="en">
<head>
<meta charset="utf-8">
<title>The Brightwater Joint Centre – Business Card</title>
<link href="https://fonts.googleapis.com/css2?family=Open+Sans:wght@300;400;600&family=PT+Sans+Narrow:wght@400;700&display=swap" rel="stylesheet">
<style>
  :root {
    --bg: #e9eaec;
    --paper: #ffffff;
    --navy-top: #0b2748;
    --navy-bottom: #041a33;
    --blue: #2a98e8;
    --ink: #4a4f55;
    --white: #ffffff;
  }
  * { box-sizing: border-box; margin: 0; padding: 0; }
  html, body { width: 1200px; height: 1040px; overflow: hidden; }
  body {
    background: var(--bg);
    font-family: "Open Sans", Arial, sans-serif;
    position: relative;
  }
  .card {
    position: absolute;
    width: 680px;
    height: 390px;
    border-radius: 22px;
    box-shadow: 0 10px 28px rgba(0,0,0,0.18);
    overflow: hidden;
  }
  .card-front { left: 80px; top: 70px; background: var(--paper); }
  .card-back {
    left: 440px; top: 580px;
    background: linear-gradient(160deg, var(--navy-top), var(--navy-bottom));
    display: flex; align-items: center; justify-content: center;
  }

  .brand-name {
    font-family: "Open Sans", Arial, sans-serif;
    font-weight: 300;
    white-space: nowrap;
    display: flex; align-items: center; gap: 12px;
  }
  .brand-dot { width: 12px; height: 12px; border-radius: 50%; }
  .card-front .brand-name {
    position: absolute; left: 270px; top: 92px;
    font-size: 26px; color: var(--blue);
  }
  .card-front .brand-dot { background: var(--blue); }
  .card-back .brand-name { font-size: 40px; color: var(--white); }
  .card-back .brand-dot { background: var(--white); width: 16px; height: 16px; }

  .holder { position: absolute; left: 44px; top: 205px; }
  .holder-name {
    font-family: "PT Sans Narrow", Arial, sans-serif;
    font-weight: 700; font-size: 30px; letter-spacing: 0.5px;
    color: var(--blue); text-transform: uppercase; line-height: 1;
  }
  .holder-role {
    font-family: "PT Sans Narrow", Arial, sans-serif;
    font-size: 19px; color: var(--ink); margin-top: 4px;
  }

  .divider {
    position: absolute; left: 44px; right: 44px; top: 272px;
    height: 1px; background: var(--blue);
  }

  .contact-list {
    position: absolute; left: 44px; top: 284px;
    list-style: none;
    font-family: "PT Sans Narrow", Arial, sans-serif;
    font-size: 18px; color: var(--ink); line-height: 23px;
  }
  .contact-list li { display: flex; align-items: center; gap: 10px; }
  .contact-list svg { width: 14px; height: 14px; fill: var(--blue); flex: none; }

  .office {
    position: absolute; right: 44px; top: 284px; text-align: right;
    font-family: "PT Sans Narrow", Arial, sans-serif;
    font-size: 18px; color: var(--ink); line-height: 23px;
  }
  .office-name { color: var(--blue); font-weight: 700; font-size: 19px; }
</style>
</head>
<body>
  <section class="card card-front">
    <div class="brand-name"><span class="brand-dot"></span>The Brightwater Joint Centre</div>

    <div class="holder">
      <p class="holder-name">Daniel Hargrove</p>
      <p class="holder-role">President</p>
    </div>

    <div class="divider"></div>

    <ul class="contact-list">
      <li><svg viewBox="0 0 16 16" aria-hidden="true"><path d="M3.6 1.2l2.3 2.9-1.3 1.6c.9 2 2.5 3.6 4.5 4.6l1.6-1.3 2.9 2.3-1.5 2.6C7 13.7 2.3 9 1 3.9z"/></svg>412-608-3927</li>
      <li><svg viewBox="0 0 16 16" aria-hidden="true"><path d="M4 1h8v14H4zM5.5 2.5v9h5v-9z"/></svg>412-608-3940</li>
      <li><svg viewBox="0 0 16 16" aria-hidden="true"><path d="M4 1h7v4H4zM2 6h12v7H2zM4 14h8v1H4z"/></svg>412-608-3951</li>
      <li><svg viewBox="0 0 16 16" aria-hidden="true"><path d="M1 3h14v10H1zM2.5 4.5L8 8.8l5.5-4.3z"/></svg>daniel@brightwaterjoint.com</li>
    </ul>

    <address class="office" style="font-style:normal">
      <p class="office-name">The Brightwater Joint Centre</p>
      <p>218 Harbourview Road</p>
      <p>Brightwater, Kelston 40218</p>
      <p>www.brightwaterjoint.com</p>
    </address>
  </section>

  <section class="card card-back">
    <div class="brand-name"><span class="brand-dot"></span>The Brightwater Joint Centre</div>
  </section>
</body>
</html>
```